brightwell - Property Management DL Card

I am after a savvy designer to cut through junk mail! so many real estate agents use flyers to promote themselves and their business and usually sales. We are a property management firm (residential) and we want to represent landlords that have existing investment properties and need a quality agent to represent them. Can you help?
DL size, will be printed and delivered to mailboxes. For a look at our website go to www.brightwellrs.com.au. Keep it simple and clutter free.
it is to be double sided - with one side to be simple and clear - just our website, logo and telephone number on the back.
attached is our logo and our telephone number is 1300 48 92 16
the above are 2 essential elements to be included + our email address: admin@brightwellrs.com.au
also attached are our transparent price list

Target Market(s)
property investors,
people that manage properties themselves
Industry/Entity Type
Property Management
- arial
Look and feel

```html
<!DOCTYPE html>
<html lang="en">
<head>
<meta charset="utf-8">
<title>brightwell – Property Management DL Card</title>
<link href="https://fonts.googleapis.com/css2?family=Open+Sans:wght@300;400;600&display=swap" rel="stylesheet">
<style>
  :root {
    --stage: #dcdcdc;
    --ink: #222222;
    --ink-soft: #333333;
    --accent-blue: #6b8d9e;
    --link-blue: #4a7f99;
    --tick: #8fa3ad;
    --panel-light: #ecebea;
    --panel-mid: #d4d1cf;
    --band: rgba(40, 38, 36, 0.72);
    --back-card: #a8a3a0;
    --logo-black: #0a0a0a;
    --white: #ffffff;
  }
  * { box-sizing: border-box; margin: 0; padding: 0; }
  html, body {
    width: 1200px; height: 1200px; overflow: hidden;
    background: var(--stage);
    font-family: "Open Sans", Arial, sans-serif;
  }
  .canvas { position: relative; width: 1200px; height: 1200px; }

  /* Front side */
  .card-front {
    position: absolute; left: 120px; top: 53px;
    width: 1000px; height: 500px; overflow: hidden;
    background: var(--panel-light);
  }
  .interior-photo {
    position: absolute; left: 0; top: 0; width: 768px; height: 500px;
  }
  .brand-panel {
    position: absolute; left: 768px; top: 0; width: 232px; height: 500px;
    background: linear-gradient(160deg, #d6d3d1 0%, var(--panel-light) 60%, #e4e2e1 100%);
  }
  .brand-panel .brand-name {
    position: absolute; left: 0; right: 0; top: 215px;
    text-align: center; font-weight: 300; font-size: 44px;
    letter-spacing: -0.5px; color: var(--ink);
  }
  .base-band {
    position: absolute; left: 0; bottom: 0; width: 1000px; height: 63px;
    background: var(--band);
  }
  .selling-points {
    position: absolute; left: 67px; top: 68px;
  }
  .selling-points h2 {
    font-weight: 400; font-size: 19.5px; color: var(--accent-blue);
    margin-left: 3px; margin-bottom: 5px;
  }
  .selling-points ul { list-style: none; }
  .selling-points li {
    display: flex; align-items: center; gap: 6px;
    font-size: 18px; color: var(--ink); height: 27px;
  }
  .selling-points svg { width: 20px; height: 20px; flex: none; }

  /* Back side */
  .card-back {
    position: absolute; left: 119px; top: 637px;
    width: 1000px; height: 500px; background: var(--back-card);
    text-align: center;
  }
  .logo-strip {
    position: absolute; left: 321px; top: 195px; width: 358px; height: 68px;
    background: linear-gradient(90deg, rgba(10,10,10,0) 0%, var(--logo-black) 22%, var(--logo-black) 78%, rgba(10,10,10,0) 100%);
    display: flex; align-items: center; justify-content: center;
  }
  .logo-strip .brand-name {
    font-weight: 300; font-size: 36px; color: var(--white); letter-spacing: -0.5px;
  }
  .contact {
    position: absolute; left: 0; right: 0; top: 273px;
    color: var(--ink-soft); font-size: 17px; letter-spacing: 0.4px;
  }
  .contact p { line-height: 24px; }
  .contact .phone {
    font-size: 21px; font-weight: 600; color: #444444; line-height: 30px; letter-spacing: 0.6px;
  }
  .contact .web { color: var(--link-blue); }
</style>
</head>
<body>
<div class="canvas">

  <section class="card-front">
    <svg class="interior-photo" viewBox="0 0 768 500" role="img"
         aria-label="Photograph of a bright modern kitchen and dining room with a wooden table, red chairs and timber cabinetry">
      <defs>
        <linearGradient id="room-light" x1="0" y1="0" x2="1" y2="1">
          <stop offset="0" stop-color="#ffffff"/>
          <stop offset="0.45" stop-color="#f1f0ee"/>
          <stop offset="0.8" stop-color="#c9b48e"/>
          <stop offset="1" stop-color="#8a6a45"/>
        </linearGradient>
        <linearGradient id="floor-tone" x1="0" y1="0" x2="0" y2="1">
          <stop offset="0" stop-color="#000" stop-opacity="0"/>
          <stop offset="1" stop-color="#6d5536" stop-opacity="0.35"/>
        </linearGradient>
      </defs>
      <rect width="768" height="500" fill="url(#room-light)"/>
      <rect width="768" height="500" fill="url(#floor-tone)"/>
    </svg>

    <div class="brand-panel">
      <span class="brand-name">brightwell</span>
    </div>

    <div class="base-band"></div>

    <div class="selling-points">
      <h2>Property Management specialists</h2>
      <ul>
        <li><svg viewBox="0 0 20 20"><circle cx="10" cy="10" r="8" fill="none" stroke="var(--tick)" stroke-width="1.6"/><path d="M6 10 l3 3 l8 -8" fill="none" stroke="var(--tick)" stroke-width="2" stroke-linecap="round"/></svg>No postage and Admin fees</li>
        <li><svg viewBox="0 0 20 20"><circle cx="10" cy="10" r="8" fill="none" stroke="var(--tick)" stroke-width="1.6"/><path d="M6 10 l3 3 l8 -8" fill="none" stroke="var(--tick)" stroke-width="2" stroke-linecap="round"/></svg>No hidden Extras</li>
        <li><svg viewBox="0 0 20 20"><circle cx="10" cy="10" r="8" fill="none" stroke="var(--tick)" stroke-width="1.6"/><path d="M6 10 l3 3 l8 -8" fill="none" stroke="var(--tick)" stroke-width="2" stroke-linecap="round"/></svg>Excellent Communication</li>
        <li><svg viewBox="0 0 20 20"><circle cx="10" cy="10" r="8" fill="none" stroke="var(--tick)" stroke-width="1.6"/><path d="M6 10 l3 3 l8 -8" fill="none" stroke="var(--tick)" stroke-width="2" stroke-linecap="round"/></svg>Technology Focussed</li>
      </ul>
    </div>
  </section>

  <section class="card-back">
    <div class="logo-strip"><span class="brand-name">brightwell</span></div>
    <div class="contact">
      <p>PO Box B327, Sydney South NSW, 1235</p>
      <p class="phone">1300 48 92 16</p>
      <p>admin@brightwellrs.com.au</p>
      <p class="web">www.brightwellrs.com.au</p>
    </div>
  </section>

</div>
</body>
</html>
```